RWT Fittings Ltd Business Cards

We need a business card with our business logo. We provide window and door installations on high-rises in west coast British Colombia, Canada.

I would like my business information and details on one side of the card, and the other side the company name with logo

Target Market(s)

General Contractors

Industry/Entity Type

Construction

Contact Information for Business Card

one side i want my company name and logo in the dark theme logo that i provided

Requirements
Must have
• Marco Peltieri, 16045518293, RWTFittings@mailbox-demo.com, 1407-5194 Linden Row Burnaby BC, V5H 2K9, Owner & Manager

```html
<!DOCTYPE html>
<html lang="en">
<head>
<meta charset="utf-8">
<title>RWT Fittings Ltd – Business Cards</title>
<link rel="stylesheet" href="https://fonts.googleapis.com/css2?family=Montserrat:wght@400;500;600;700&display=swap">
<style>
  :root {
    --stage: #3c3c3c;
    --card-white: #ffffff;
    --card-black: #181818;
    --brand-blue: #27a6e1;
    --brand-grey: #9a9a9a;
    --ink-dark: #2a2a2a;
    --ink-light: #f2f2f2;
  }
  * { box-sizing: border-box; margin: 0; padding: 0; }
  html, body {
    width: 1200px; height: 780px; overflow: hidden;
    background: var(--stage);
    font-family: "Montserrat", sans-serif;
  }
  .canvas { position: relative; width: 1200px; height: 780px; }
  .card {
    position: absolute; top: 235px;
    width: 540px; height: 310px;
    border-radius: 3px; overflow: hidden;
    box-shadow: 0 18px 40px rgba(0,0,0,.45);
  }
  .card-front { left: 40px; background: var(--card-white); }
  .card-back  { left: 620px; background: var(--card-black); }

  .front-waves { position: absolute; inset: 0; width: 100%; height: 100%; }

  .name-block { position: absolute; left: 0; top: 22px; padding-left: 28px; }
  .name-bar {
    position: absolute; left: 0; top: 0;
    width: 16px; height: 22px; background: var(--brand-blue);
  }
  .person-name {
    font-size: 18px; font-weight: 700; letter-spacing: .5px;
    color: var(--brand-blue); text-transform: uppercase; line-height: 22px;
  }
  .person-title {
    font-size: 11.5px; font-weight: 400; color: var(--ink-dark); margin-top: 2px;
  }

  .contact-list {
    position: absolute; left: 22px; top: 178px;
    list-style: none; color: var(--ink-light);
    font-size: 10.5px; line-height: 17px;
  }
  .contact-address { margin-bottom: 4px; }
  .contact-item { display: flex; align-items: center; gap: 6px; }
  .contact-icon { width: 11px; height: 11px; flex: none; }

  .front-brand {
    position: absolute; left: 272px; top: 122px;
    display: flex; align-items: center; gap: 10px;
  }
  .brand-square {
    width: 22px; height: 22px; background: var(--brand-grey); flex: none;
  }
  .brand-name {
    font-size: 24px; font-weight: 600; color: var(--brand-blue);
    line-height: 1; white-space: nowrap;
  }

  .back-pattern {
    position: absolute; inset: 0;
    background: linear-gradient(135deg, #222 0%, #151515 55%, #0e0e0e 100%);
  }
  .back-brand {
    position: absolute; inset: 0;
    display: flex; align-items: center; justify-content: center; gap: 10px;
  }
</style>
</head>
<body>
<main class="canvas">

  <section class="card card-front" aria-label="Business card front">
    <svg class="front-waves" viewBox="0 0 540 310" preserveAspectRatio="none" aria-hidden="true">
      <path d="M140,80 C215,88 262,135 300,205 C330,262 380,292 470,306"
            fill="none" stroke="var(--brand-grey)" stroke-width="5"/>
      <path d="M0,138 C120,102 205,128 258,210 C300,272 400,300 520,310 L540,310 L540,300 C410,292 320,262 275,200 C225,120 130,96 0,128 Z"
            fill="var(--brand-blue)"/>
      <path d="M0,150 C115,116 195,140 246,222 C286,284 380,306 500,310 L0,310 Z"
            fill="var(--card-black)"/>
    </svg>

    <div class="name-block">
      <span class="name-bar"></span>
      <h1 class="person-name">Marco Peltieri</h1>
      <p class="person-title">Owner &amp; Manager</p>
    </div>

    <ul class="contact-list">
      <li class="contact-address">1407-5194 Linden Row Burnaby BC,<br>V5H 2K9</li>
      <li class="contact-item">
        <svg class="contact-icon" viewBox="0 0 12 12" aria-hidden="true">
          <path d="M3,1 L5,3.5 L4,5 C4.6,6.4 5.6,7.4 7,8 L8.5,7 L11,9 L10,11 C5.5,11 1,6.5 1,2 Z" fill="var(--brand-blue)"/>
        </svg>
        <span>16045518293</span>
      </li>
      <li class="contact-item">
        <svg class="contact-icon" viewBox="0 0 12 12" aria-hidden="true">
          <rect x="1" y="2.5" width="10" height="7" fill="var(--brand-blue)"/>
          <path d="M1,2.5 L6,6.5 L11,2.5" fill="none" stroke="var(--card-black)" stroke-width="1"/>
        </svg>
        <span>RWTFittings@mailbox-demo.com</span>
      </li>
      <li class="contact-item">
        <svg class="contact-icon" viewBox="0 0 12 12" aria-hidden="true">
          <circle cx="6" cy="6" r="5" fill="var(--brand-blue)"/>
          <path d="M1,6 H11 M6,1 C3.5,4 3.5,8 6,11 M6,1 C8.5,4 8.5,8 6,11" fill="none" stroke="var(--card-black)" stroke-width=".8"/>
        </svg>
        <span>www.rwtfittings-demo.com</span>
      </li>
    </ul>

    <div class="front-brand">
      <span class="brand-square"></span>
      <span class="brand-name">RWT Fittings Ltd</span>
    </div>
  </section>

  <section class="card card-back" aria-label="Business card back">
    <div class="back-pattern" role="img" aria-label="Dark repeating pattern of building shapes"></div>
    <div class="back-brand">
      <span class="brand-square"></span>
      <span class="brand-name">RWT Fittings Ltd</span>
    </div>
  </section>

</main>
</body>
</html>
```